Card Design for my dog training business Brightpaw Obedience

Need a business card design for my dog training business with my new logo. Want the card to come off professional yet fun. Want it to be very eye catchy as well. I normally have these at vet clinics, pet stores, and groomers. so need it to look better than my competitors.
Target Market(s)
dog owners
Industry/Entity Type
Dog Training
Contact Information for Business Card
needs logo, my name and info
Font styles to use
Serif
Colors
0255a3
ffffff
ec1f27
000000
333333
fbfbfb
Requirements
Must have
- Brightpaw Obedience
- Felix Orland
- 415 903 2276
- info@brightpawobedience.example
- www.brightpawobedience.example

```html
<!DOCTYPE html>
<html lang="en">
<head>
<meta charset="UTF-8">
<title>Brightpaw Obedience – Business Card</title>
<link rel="stylesheet" href="https://fonts.googleapis.com/css2?family=Noto+Serif:wght@400&family=EB+Garamond:ital@1&display=swap">
<style>
  :root {
    --backdrop: #3b3b3d;
    --card: #1d1e21;
    --silver: #c9cacc;
    --silver-soft: #a9abae;
    --accent-blue: #1b8fd2;
    --muted: #9a9b9e;
  }
  * { margin: 0; padding: 0; box-sizing: border-box; }
  html, body {
    width: 799px; height: 1200px; overflow: hidden;
    background: var(--backdrop);
  }
  .sheet {
    width: 799px; height: 1200px;
    display: flex; flex-direction: column;
    justify-content: space-around; align-items: center;
    padding: 40px 0;
  }
  .card {
    width: 660px; height: 378px;
    background: var(--card);
    border-radius: 3px;
    box-shadow: 0 14px 30px rgba(0,0,0,0.45);
    position: relative;
    font-family: "Noto Serif", serif;
  }

  /* Front */
  .card-front {
    display: flex; flex-direction: column;
    align-items: center; justify-content: center;
  }
  .front-mark {
    display: flex; align-items: center; gap: 14px;
    margin-top: -10px;
  }
  .mark-square {
    width: 22px; height: 22px;
    background: var(--silver);
  }
  .brand-name {
    font-family: "Noto Serif", serif;
    font-weight: 400;
    color: var(--silver);
    font-size: 38px;
    letter-spacing: 0.5px;
  }
  .tagline {
    margin-top: 44px;
    font-family: "EB Garamond", serif;
    font-style: italic;
    font-size: 19px;
    color: var(--silver-soft);
  }

  /* Back */
  .card-back {
    display: flex; align-items: center;
    padding: 0 40px 0 58px;
  }
  .back-mark {
    width: 230px;
    display: flex; flex-direction: column; align-items: flex-start; gap: 12px;
    margin-top: -50px;
  }
  .back-mark .brand-name {
    font-size: 30px; line-height: 1.15;
  }
  .contact-block {
    margin-left: 44px;
    margin-top: 40px;
  }
  .person-name {
    font-size: 25px;
    font-weight: 400;
    color: var(--accent-blue);
    line-height: 1.1;
  }
  .person-role {
    font-size: 14px;
    color: var(--muted);
    margin-bottom: 16px;
  }
  .contact-list { list-style: none; }
  .contact-list li {
    display: flex; align-items: center; gap: 12px;
    font-size: 14.5px; color: var(--silver);
    line-height: 1.75;
    white-space: nowrap;
  }
  .contact-list svg { width: 13px; height: 13px; flex: none; fill: var(--accent-blue); }
</style>
</head>
<body>
<main class="sheet">

  <section class="card card-front" aria-label="Card front">
    <div class="front-mark">
      <span class="mark-square"></span>
      <span class="brand-name">Brightpaw Obedience</span>
    </div>
    <p class="tagline">“Building good manners, one happy dog at a time.”</p>
  </section>

  <section class="card card-back" aria-label="Card back">
    <div class="back-mark">
      <span class="mark-square"></span>
      <span class="brand-name">Brightpaw<br>Obedience</span>
    </div>
    <div class="contact-block">
      <h1 class="person-name">Felix Orland</h1>
      <p class="person-role">Dog Trainer</p>
      <ul class="contact-list">
        <li>
          <svg viewBox="0 0 16 16" aria-hidden="true"><path d="M3.6 1.2 6 3.6 4.7 5.6c.9 2 2.4 3.5 4.4 4.4l2-1.3 2.4 2.4-1.6 2.3C6.7 13.5 2.5 9.3 1.3 3z"/></svg>
          415 903 2276
        </li>
        <li>
          <svg viewBox="0 0 16 16" aria-hidden="true"><path d="M1 3h14v10H1z M2 4.2v.4l6 4 6-4v-.4z" fill-rule="evenodd"/></svg>
          info@brightpawobedience.example
        </li>
        <li>
          <svg viewBox="0 0 16 16" aria-hidden="true"><path d="M8 1a7 7 0 1 0 0 14A7 7 0 0 0 8 1zm0 1.4c.8.9 1.4 2.4 1.6 4.1H6.4C6.6 4.8 7.2 3.3 8 2.4zM6.4 7.9h3.2c-.2 1.7-.8 3.2-1.6 4.1-.8-.9-1.4-2.4-1.6-4.1zM2.5 7.9h2.5c.1 1.5.5 2.9 1.1 3.9A5.6 5.6 0 0 1 2.5 7.9zm8.5 0h2.5a5.6 5.6 0 0 1-3.6 3.9c.6-1 1-2.4 1.1-3.9zM2.5 6.5a5.6 5.6 0 0 1 3.6-3.9c-.6 1-1 2.4-1.1 3.9zm8.5 0c-.1-1.5-.5-2.9-1.1-3.9a5.6 5.6 0 0 1 3.6 3.9z"/></svg>
          www.brightpawobedience.example
        </li>
      </ul>
    </div>
  </section>

</main>
</body>
</html>
```